RW Framewell Inc Business cards

We need business cards using our existing logo but slightly modified. Right now the logo says RW Loadbearing Masonry. We want to keep the RW part of the design, but replace the Structural Concrete portion with "FRAMEWELL". Please see the attached file.
Ideally this would be a blank template so we can add Different Names, titles, and phone numbers later.
On the one side we want only the logo and on the other side the detail. I'm attaching an example for you to see.
Please reach out with any other questions. Our address and other details will be given out once we find a design we like.

Target Market(s)

Construction Industry

```html
<!DOCTYPE html>
<html lang="en">
<head>
<meta charset="utf-8">
<title>RW Framewell Inc — Business Card</title>
<link href="https://fonts.googleapis.com/css2?family=Montserrat:wght@600&family=Roboto:wght@400;500&display=swap" rel="stylesheet">
<style>
  :root {
    --page-bg: #d9d6d1;
    --card-bg: #eef0ef;
    --brand-blue: #2f5d9e;
    --text-grey: #56595c;
    --band-text: #e9eef5;
  }
  html, body {
    margin: 0;
    padding: 0;
    width: 1200px;
    height: 1054px;
    overflow: hidden;
    background: var(--page-bg);
  }
  .card {
    position: absolute;
    left: 100px;
    top: 227px;
    width: 1000px;
    height: 600px;
    background: var(--card-bg);
    box-shadow: 0 10px 30px rgba(0,0,0,0.12);
    overflow: hidden;
    font-family: "Roboto", Arial, sans-serif;
    color: var(--text-grey);
  }
  .holder-name {
    position: absolute;
    left: 62px;
    top: 82px;
    margin: 0;
    font-family: "Montserrat", Arial, sans-serif;
    font-weight: 600;
    font-size: 33px;
    color: var(--brand-blue);
  }
  .holder-title {
    position: absolute;
    left: 62px;
    top: 128px;
    margin: 0;
    font-size: 24px;
  }
  .brand {
    position: absolute;
    right: 70px;
    top: 70px;
    text-align: center;
    font-family: "Montserrat", Arial, sans-serif;
    font-weight: 600;
    color: var(--brand-blue);
  }
  .brand-initials {
    display: block;
    font-size: 150px;
    line-height: 150px;
    letter-spacing: 4px;
  }
  .brand-name {
    display: block;
    font-size: 38px;
    letter-spacing: 7px;
    margin-top: 8px;
  }
  .contact {
    position: absolute;
    left: 62px;
    top: 384px;
    margin: 0;
    padding: 0;
    list-style: none;
    font-size: 24px;
  }
  .contact-line {
    display: flex;
    align-items: center;
    height: 38px;
  }
  .contact-icon {
    width: 24px;
    height: 20px;
    margin-right: 26px;
    fill: var(--brand-blue);
  }
  .contact-address {
    margin-top: 12px;
    line-height: 38px;
  }
  .web-band {
    position: absolute;
    left: 0;
    bottom: 0;
    width: 1000px;
    height: 74px;
  }
  .web-band polygon { fill: var(--brand-blue); }
  .web-address {
    position: absolute;
    right: 110px;
    bottom: 20px;
    font-weight: 500;
    font-size: 26px;
    color: var(--band-text);
  }
</style>
</head>
<body>
  <section class="card">
    <h1 class="holder-name">Mark RW Dalton</h1>
    <p class="holder-title">Managing Director</p>

    <div class="brand" aria-label="RW Framewell">
      <span class="brand-initials">RW</span>
      <span class="brand-name">FRAMEWELL</span>
    </div>

    <ul class="contact">
      <li class="contact-line">
        <svg class="contact-icon" viewBox="0 0 24 20" aria-hidden="true">
          <path d="M2 5c0-2 3-4 10-4s10 2 10 4v2h-5V5H7v2H2z"/>
          <path d="M5 9h14l2 9H3z"/>
        </svg>
        <span>555-014-2290</span>
      </li>
      <li class="contact-line">
        <svg class="contact-icon" viewBox="0 0 24 20" aria-hidden="true">
          <path d="M1 3h22v2l-11 7L1 5z"/>
          <path d="M1 7l11 7 11-7v10H1z"/>
        </svg>
        <span>mark@framewellbuild.com</span>
      </li>
      <li class="contact-address">17 Timberline Rd., Oakridge,<br>Oregon, US 97463</li>
    </ul>

    <svg class="web-band" viewBox="0 0 1000 74" aria-hidden="true">
      <polygon points="530,0 1000,0 1000,74 485,74"/>
    </svg>
    <span class="web-address">www.framewellbuild.com</span>
  </section>
</body>
</html>
```